Business Card Design

Just looking for a good designs that looks good with our company logo. I'd like it to be simple and to the point. Just including contact information, our logo, and my name somewhere on the card so future clients know who they're contacting, and a couple services offered. The two images I attached are pictures of our logo. I don't care which color they they are, I just attached both images to give a reference of logo colors depending on the color of the card.
Names: Carl Whitby
Phone: 816-555-0147
Email: greenstripeyard@fernmail.test
Services offered:
Mowing
Fertilization
Aeration
Bed & tree maintenance
and more.
Business
Names: Carl Whitby
Phone: 816-555-0147
(no website)

```html
<!DOCTYPE html>
<html lang="en">
<head>
<meta charset="utf-8">
<title>Fieldline Lawn &amp; Landscape – Business Card</title>
<link rel="stylesheet" href="https://fonts.googleapis.com/css2?family=Merriweather:wght@300;700&family=Noto+Serif:ital@1&family=PT+Serif&display=swap">
<style>
  :root {
    --paper: #e6e7e4;
    --coral: #f26e50;
    --navy: #10386b;
    --ink: #343744;
    --badge: #2a1f55;
    --service-blue: #5a67b4;
    --service-red: #e9553f;
    --white: #ffffff;
    --dark-text: #1a1a22;
  }
  html, body { margin: 0; padding: 0; overflow: hidden; background: var(--paper); }
  .card {
    position: relative;
    width: 1200px;
    height: 702px;
    overflow: hidden;
    background: radial-gradient(ellipse at 50% 40%, #eeefec 0%, var(--paper) 70%);
  }
  .contact-tab {
    position: absolute;
    display: flex;
    align-items: center;
    box-sizing: border-box;
    background: var(--coral);
    border-radius: 4px 0 0 4px;
    white-space: nowrap;
  }
  .contact-tab::after {
    content: "";
    position: absolute;
    left: 1121px;
    top: 50%;
    width: 16px;
    height: 22px;
    transform: translateY(-50%);
    background: var(--navy);
  }
  .name-tab {
    left: 683px; top: 56px; width: 517px; height: 83px;
    justify-content: flex-end;
    padding-right: 88px;
    color: var(--white);
    font: 300 37px/1 "Merriweather", serif;
    letter-spacing: 1px;
  }
  .name-tab::after { left: 438px; }
  .phone-tab {
    left: 814px; top: 157px; width: 386px; height: 64px;
    padding-left: 11px;
    color: var(--dark-text);
    font: 400 37px/1 "PT Serif", serif;
    letter-spacing: 1.5px;
  }
  .phone-tab::after { left: 307px; }
  .phone-icon { width: 32px; height: 32px; margin-right: 6px; flex: none; }
  .email-tab {
    left: 814px; top: 239px; width: 386px; height: 64px;
    padding-left: 16px;
    color: var(--dark-text);
    font: 400 19px/1 "PT Serif", serif;
  }
  .email-tab::after { left: 307px; }
  .quality-badge {
    position: absolute;
    left: 180px; top: 224px;
    width: 240px; height: 70px;
  }
  .brand {
    position: absolute;
    left: 440px; top: 262px;
    width: 330px;
    text-align: center;
    font: 700 34px/1.2 "Merriweather", serif;
    color: var(--ink);
  }
  .services {
    position: absolute;
    left: 0; top: 456px;
    width: 1200px;
    font: italic 400 35px/1 "Noto Serif", serif;
  }
  .services p { margin: 0; position: absolute; white-space: nowrap; }
  .services .line-one { left: 342px; top: 0; color: var(--service-blue); }
  .services .line-one .accent { color: var(--service-red); }
  .services .line-two { left: 365px; top: 46px; color: var(--service-red); }
  .services .line-three { left: 518px; top: 92px; color: var(--service-blue); }
  .landscape {
    position: absolute;
    left: 0; top: 596px;
    width: 1200px; height: 106px;
    background: linear-gradient(to bottom, rgba(52,55,68,0) 0%, rgba(52,55,68,0.75) 25%, var(--ink) 45%);
  }
</style>
</head>
<body>
<main class="card">
  <div class="landscape" role="img" aria-label="Silhouette of trees on grassy ground"></div>

  <div class="contact-tab name-tab">Carl Whitby</div>
  <div class="contact-tab phone-tab">
    <svg class="phone-icon" viewBox="0 0 32 32" aria-hidden="true">
      <rect width="32" height="32" rx="5" fill="#10386b"/>
      <path d="M11 7c1 0 2 3 2.5 4.5.3 1-1.5 2-1.5 2.5 0 1.5 3.5 6 5 6.5.6.2 1.8-1.5 2.6-1.2 1.5.6 4.4 1.8 4.4 2.7 0 1.5-2 3.5-4 3.5C14 25.5 7 17 7 11c0-2 2-4 4-4z" fill="#ffffff"/>
    </svg>
    816-555-0147
  </div>
  <div class="contact-tab email-tab">greenstripeyard@fernmail.test</div>

  <svg class="quality-badge" viewBox="0 0 240 70" role="img" aria-label="Quality guarantee badge">
    <polygon points="0,14 240,0 236,48 0,70" fill="#2a1f55"/>
  </svg>

  <div class="brand">Fieldline<br>Lawn &amp; Landscape</div>

  <section class="services">
    <p class="line-one">Mowing <span class="accent">.Fertilization</span> .Aeration</p>
    <p class="line-two">Bed and tree maintenance</p>
    <p class="line-three">and more ...</p>
  </section>
</main>
</body>
</html>
```